Web Design Project

Psychotherapy and Counselling Practice needs a landing page web design.

My business "Larkfield Advisory" specialises in the treatment of Anxiety and Depression with a holistic approach, endeavouring to unlock the key that holds us to ransom in a life that is imbalanced, frustrating, and ultimately of our own making due to our own perceptions and behaviours.

There is much that impacts us which we cannot change, but we are always in control of how we think, and how we frame our experiences.....learning to challenge those thoughts and behaviours that are destructive and disempowering opens up a world of joyful possibility. Life is about making choices, learn to make wiser and healthier choices.......

Larkfield Advisory has a client base of individual clients but will seek to expand to offer services to the Corporate world by offering an adjunct to employers for established "Wellness Programs".

Larkfield Advisory is a highly professional, ethically bound business, with the needs of the client at the forefront of all we do.

Larkfield Advisory wishes to avoid the usual "jargon driven" psychobabble offered on many counselling web pages. It aims to be stylishly presented, clean in look and with as few "words" as possible and a largely white background (faster loading and more powerful impact of what is stated), those words contained in the webpage should be meaningful, persuasive and have an impact simply at glance. Larkfield does not want , or expect, those prospective clients in need of support , to be reading through volumes of industry driven cliches.

At this point Larkfield is just looking for a high quality landing page. However in time this will likely expand to include other sections such as case studies, video content etc.

Target Market(s)

Those in need of emotional support, suffering mental health issues, and those simply wanting to become self aware supported by a mindful therapist.

Industry/Entity Type

Industry

Requirements
Must have
• The design must incorporate the Larkfield logo and colour schemes found on the attached files.

```html
<!DOCTYPE html>
<html lang="en">
<head>
<meta charset="utf-8">
<title>Larkfield Advisory</title>
<link rel="stylesheet" href="https://fonts.googleapis.com/css2?family=Big+Shoulders+Display:wght@200;300&family=Open+Sans:wght@300;400;600;700&display=swap">
<style>
  :root {
    --green: #8aac0e;
    --grey: #717171;
    --text: #6e6e6e;
    --muted: #9a9a9a;
    --rule: #d8d8d8;
    --white: #ffffff;
    --icon: #3a3a3a;
  }
  * { margin: 0; padding: 0; box-sizing: border-box; }
  html, body { width: 1200px; height: 1000px; overflow: hidden; background: var(--white); }
  body { position: relative; font-family: "Open Sans", sans-serif; color: var(--text); }

  .site-nav { position: absolute; left: 120px; top: 0; width: 961px; height: 70px; border-bottom: 1px solid var(--rule); }
  .site-nav ul { list-style: none; position: absolute; right: 0; top: 21px; display: flex; }
  .site-nav li { font-size: 13.5px; color: var(--green); text-transform: uppercase; height: 49px; line-height: 46px; padding: 0 18px; white-space: nowrap; }
  .site-nav li.current { border: 1px solid #d6dfb6; border-bottom: 1px solid var(--white); border-radius: 3px 3px 0 0; background: var(--white); margin-bottom: -1px; }
  .site-nav li:last-child { padding-right: 0; padding-left: 22px; }

  .vine { position: absolute; left: 258px; top: 85px; width: 84px; height: 581px; background: linear-gradient(180deg, #c9da8f, #9dba36 60%, #b3cb5e); opacity: .45; border-radius: 40px 40px 0 0; }
  .brand { position: absolute; left: 118px; top: 262px; width: 404px; text-align: center; font-weight: 300; font-size: 62px; letter-spacing: 9px; padding-left: 9px; color: var(--grey); line-height: 80px; white-space: nowrap; }

  .quote { position: absolute; left: 540px; top: 112px; width: 530px; text-align: center; font-family: "Big Shoulders Display", sans-serif; font-weight: 200; font-size: 60px; line-height: 61px; color: var(--grey); text-transform: uppercase; white-space: nowrap; }
  .attribution { position: absolute; left: 765px; top: 296px; width: 194px; height: 55px; }
  .attribution span { position: absolute; left: 0; top: 16px; width: 194px; height: 39px; line-height: 39px; background: var(--green); color: var(--white); border-radius: 5px; text-align: center; font-family: "Big Shoulders Display", sans-serif; font-weight: 300; font-size: 20px; text-transform: uppercase; letter-spacing: 1px; }
  .attribution svg { position: absolute; left: 19px; top: 0; }

  .pitch { position: absolute; left: 560px; top: 418px; width: 520px; text-align: center; font-size: 22px; line-height: 29px; color: var(--text); white-space: nowrap; }
  .pitch em { font-style: normal; color: var(--green); }

  .contact { position: absolute; left: 615px; top: 487px; width: 411px; height: 163px; border-top: 1px solid #cddca0; border-bottom: 1px solid var(--rule); text-align: center; }
  .contact .call { margin-top: 11px; font-size: 17px; line-height: 24px; color: var(--green); }
  .contact .name { margin-top: 12px; font-size: 24px; font-weight: 700; color: var(--grey); line-height: 28px; }
  .contact .creds { font-size: 11px; line-height: 16px; color: var(--muted); }
  .contact .line { font-size: 13.5px; font-weight: 600; color: var(--text); line-height: 22px; }
  .contact .mobile { margin-top: 13px; }

  .band { position: absolute; left: 0; top: 666px; width: 1200px; height: 20px; background: var(--green); }
  .footer { position: absolute; left: 0; top: 686px; width: 1200px; height: 94px; background: var(--grey); }
  .social { position: absolute; left: 137px; top: 17px; }
  .copyright { position: absolute; left: 138px; top: 66px; font-size: 11px; font-weight: 600; color: var(--white); }
  .web { position: absolute; left: 662px; top: 28px; font-size: 22px; color: var(--green); }
  .web small { font-size: 15px; }
</style>
</head>
<body>
  <nav class="site-nav">
    <ul>
      <li class="current">Home</li>
      <li>About Larkfield</li>
      <li>Contact Us</li>
    </ul>
  </nav>

  <div class="vine" role="img" aria-label="Climbing green vine illustration"></div>
  <div class="brand">LARKFIELD</div>

  <p class="quote">Just living is not enough. One<br>must have sunshine, freedom,<br>and a little flower.</p>
  <div class="attribution">
    <svg width="18" height="18" viewBox="0 0 18 18"><polygon points="0,0 18,18 0,18" fill="#8aac0e"/></svg>
    <span>E. M. Hartwell</span>
  </div>

  <p class="pitch">“Larkfield is here to help you<br>find the <em>sunshine</em>, <em>freedom</em> and <em>little flower</em>”</p>

  <section class="contact">
    <p class="call">Call Us Today:</p>
    <p class="name">MARA ELLISON</p>
    <p class="creds">BA (Psych) BSc (Hons) Psych MBPS</p>
    <p class="line mobile">Mobile: 0412 555 018</p>
    <p class="line">E-mail: mara.ellison@larkmail.com</p>
  </section>

  <div class="band"></div>
  <footer class="footer">
    <svg class="social" width="180" height="36" viewBox="0 0 180 36" aria-label="Social links">
      <circle cx="17" cy="18" r="17" fill="#3a3a3a"/>
      <circle cx="65" cy="18" r="17" fill="#3a3a3a"/>
      <circle cx="113" cy="18" r="17" fill="#3a3a3a"/>
      <circle cx="160" cy="18" r="17" fill="#3a3a3a"/>
    </svg>
    <p class="copyright">Copyright © 2013 LARKFIELD - All rights reserved</p>
    <p class="web"><small>www.</small>larkfieldadvisory<small>.com.au</small></p>
  </footer>
</body>
</html>
```